Optical shop needs a signage that attracts families such as parents and kids

My shop name is Mivo optical. I need a signage for my optical shop that can attract families, targeting mainly kids and their adults. My shop is situated in neighborhood areas and sells affordable spectacles. The interior of my shop is clean and white base, very comfortable feeling that makes people feel like they have come home. Signage should not be too fancy and colourful. I have attached a mascot for my signage too, it is a cat that wear spectacles. You can either use or don't use the mascot for the design. Let me view your creative side. :)

The theme would be more of Japanese. Please do something that has Japanese style or elements for the signage logo design. Colours used can be more of Japanese origin.
Updates

Reason: There are not enough designs to choose from. Please help to send in more designs. Thanks.

The theme would be more Japanese style as people would like to associate my shop name with it.

Target Market(s)

Families, teens and elderly

Industry/Entity Type

Shop

Font styles to use
Script

```html
<!DOCTYPE html>
<html lang="en">
<head>
<meta charset="utf-8">
<title>Mivo optical – signage options</title>
<link rel="stylesheet" href="https://fonts.googleapis.com/css2?family=Pacifico&display=swap">
<style>
  :root {
    --paper: #ffffff;
    --frame: #333333;
    --ink: #111111;
    --sun-red: #d2393b;
    --mascot-tone: #f1ece6;
    --label: #000000;
  }
  html, body {
    margin: 0;
    padding: 0;
    width: 1200px;
    height: 848px;
    overflow: hidden;
    background: var(--paper);
  }
  .sheet {
    position: relative;
    width: 1200px;
    height: 848px;
    font-family: Arial, Helvetica, sans-serif;
    color: var(--label);
  }
  .dimension, .option-label {
    position: absolute;
    font-size: 17px;
    line-height: 1;
  }
  .dimension--width { left: 589px; top: 46px; }
  .dimension--height { left: 987px; top: 189px; }
  .option-label { left: 118px; }
  .option-label--a { top: 175px; }
  .option-label--b { top: 425px; }
  .option-label--c { top: 672px; }

  .signboard {
    position: absolute;
    left: 267px;
    width: 709px;
    height: 227px;
    box-sizing: border-box;
    border: 1px solid var(--frame);
    background: var(--paper);
    overflow: hidden;
  }
  .signboard--a { top: 72px; }
  .signboard--b { top: 322px; }
  .signboard--c { top: 573px; }

  .signboard__art {
    position: absolute;
    inset: 0;
    width: 100%;
    height: 100%;
  }
  .sun { fill: var(--sun-red); }
  .mascot { fill: var(--mascot-tone); }

  .shop-name {
    position: absolute;
    font-family: "Pacifico", cursive;
    font-weight: 400;
    white-space: nowrap;
    line-height: 1;
  }
  .shop-name--split-first {
    left: 178px;
    top: 48px;
    font-size: 62px;
    color: var(--paper);
  }
  .shop-name--split-second {
    left: 374px;
    top: 64px;
    font-size: 46px;
    color: var(--sun-red);
  }
  .shop-name--inline {
    left: 86px;
    top: 150px;
    font-size: 46px;
  }
  .shop-name--black { color: var(--ink); }
  .shop-name--red { color: var(--sun-red); }
</style>
</head>
<body>
<main class="sheet">
  <span class="dimension dimension--width">250cm</span>
  <span class="dimension dimension--height">80cm</span>

  <span class="option-label option-label--a">A</span>
  <span class="option-label option-label--b">B</span>
  <span class="option-label option-label--c">C</span>

  <section class="signboard signboard--a" aria-label="Option A">
    <svg class="signboard__art" viewBox="0 0 709 227">
      <circle class="sun" cx="258" cy="116" r="105"/>
      <rect class="mascot" x="156" y="110" width="118" height="117" rx="18" role="img" aria-label="Mascot illustration: waving cat wearing spectacles with cherry blossoms"/>
    </svg>
    <span class="shop-name shop-name--split-first">Mivo</span>
    <span class="shop-name shop-name--split-second">optical</span>
  </section>

  <section class="signboard signboard--b" aria-label="Option B">
    <svg class="signboard__art" viewBox="0 0 709 227">
      <circle class="sun" cx="538" cy="115" r="98"/>
      <rect class="mascot" x="436" y="72" width="158" height="155" rx="22" role="img" aria-label="Mascot illustration: waving cat wearing spectacles with cherry blossoms"/>
    </svg>
    <span class="shop-name shop-name--inline shop-name--black">Mivo optical</span>
  </section>

  <section class="signboard signboard--c" aria-label="Option C">
    <svg class="signboard__art" viewBox="0 0 709 227">
      <circle class="sun" cx="538" cy="115" r="98"/>
      <rect class="mascot" x="436" y="72" width="158" height="155" rx="22" role="img" aria-label="Mascot illustration: waving cat wearing spectacles with cherry blossoms"/>
    </svg>
    <span class="shop-name shop-name--inline shop-name--red">Mivo optical</span>
  </section>
</main>
</body>
</html>
```